Oakmere Animal Care Group of Central Pennsylvania

I need a business card design for a new company in Harrisburg PA called "Animal Care Oakmere Group of Central PA". I will be providing relief services for veterinarians who need coverage during vacations; sick/maternity leave, etc. I would like to see the veterinarian symbol incorporated in the design in combination with animals (dogs /cats/birds/reptiles an pocket pets). Include My full name: Tomás R. Quintaval DVM, MLAS, BS. Also include my e mail (dvmtrq@mailbrook.net) and phone number 5552846017

Target Market(s)

Small Animal Veterinarian, practice owner

Industry/Entity Type

Business

Contact Information for Business Card

Oakmere Animal Care Group of Central PA

Font styles to use
Script

Requirements
Must have
• Veterinarian caduceus (see image) and Small animals (pets) within the logo.
Nice to have
• Give a sense of relaxation (vacationing)
Should not have
• Large animals, i.e. horses, cows, zoo animals...

```html
<!DOCTYPE html>
<html lang="en">
<head>
<meta charset="utf-8">
<title>Animal Care Oakmere Group of Central PA – Business Card</title>
<link href="https://fonts.googleapis.com/css2?family=Cinzel:wght@600&family=Courgette&family=Lora:wght@400&display=swap" rel="stylesheet">
<style>
  :root {
    --page-bg: #e9e7e3;
    --card-white: #f7f7f6;
    --card-white-shade: #e6e6e4;
    --brand-red: #c42733;
    --brand-red-deep: #9e1a24;
    --brand-red-light: #d93a46;
    --ink: #1b1b1b;
    --on-red: #ffffff;
    --on-red-soft: rgba(255,255,255,.85);
    --photo-light: #efefed;
    --photo-mid: #8a6a4a;
    --photo-dark: #3a2e25;
  }
  * { box-sizing: border-box; margin: 0; padding: 0; }
  html, body {
    width: 1200px; height: 892px; overflow: hidden;
    background: var(--page-bg);
  }
  .canvas {
    width: 1200px; height: 892px;
    display: flex; align-items: center; justify-content: center;
  }
  .card {
    position: relative;
    width: 1000px; height: 572px;
    background: linear-gradient(160deg, var(--card-white) 0%, var(--card-white) 60%, var(--card-white-shade) 100%);
    box-shadow: 0 14px 40px rgba(0,0,0,.18);
    overflow: hidden;
  }
  .card__upper {
    position: absolute; left: 0; top: 0; width: 100%; height: 392px;
  }
  .pet-photo {
    position: absolute; right: 0; top: 0; width: 470px; height: 392px;
    background:
      radial-gradient(ellipse 45% 55% at 58% 40%, var(--photo-dark) 0%, var(--photo-mid) 55%, rgba(138,106,74,0) 100%),
      radial-gradient(ellipse 30% 40% at 22% 62%, #d9d2c8 0%, rgba(217,210,200,0) 100%),
      linear-gradient(180deg, var(--photo-light), #e3e2df);
  }
  .brand {
    position: absolute; left: 70px; top: 150px;
    display: flex; align-items: center; gap: 22px;
  }
  .brand__dot {
    width: 74px; height: 74px; border-radius: 50%;
    border: 5px solid var(--brand-red);
    flex: none;
  }
  .brand__name {
    font-family: "Cinzel", serif; font-weight: 600;
    font-size: 22px; line-height: 1.3; letter-spacing: .5px;
    color: var(--ink);
    width: 330px;
  }
  .card__rule {
    position: absolute; left: 0; top: 392px; width: 100%; height: 9px;
    background: var(--ink);
  }
  .card__band {
    position: absolute; left: 0; top: 401px; width: 100%; height: 171px;
    background: linear-gradient(180deg, var(--brand-red-light) 0%, var(--brand-red) 45%, var(--brand-red-deep) 100%);
  }
  .holder {
    position: absolute; left: 60px; top: 36px; width: 450px;
    color: var(--on-red);
  }
  .holder__name {
    font-family: "Courgette", cursive; font-size: 42px; line-height: 1.2;
    white-space: nowrap;
  }
  .holder__credentials {
    margin-top: 6px;
    font-family: "Lora", serif; font-size: 18px; letter-spacing: 1.5px;
    color: var(--on-red-soft);
  }
  .band-divider {
    position: absolute; left: 530px; top: 28px; width: 2px; height: 115px;
    background: linear-gradient(180deg, rgba(255,255,255,0), rgba(255,255,255,.55), rgba(255,255,255,0));
  }
  .contact {
    position: absolute; left: 580px; top: 42px;
    list-style: none;
    font-family: "Lora", serif; font-size: 23px; color: var(--on-red);
  }
  .contact__item { display: flex; align-items: center; gap: 18px; height: 44px; }
  .contact__icon { width: 20px; height: 20px; fill: var(--on-red); flex: none; }
</style>
</head>
<body>
<main class="canvas">
  <article class="card">
    <section class="card__upper">
      <div class="brand">
        <span class="brand__dot"></span>
        <h1 class="brand__name">Animal Care Oakmere Group of Central PA</h1>
      </div>
      <div class="pet-photo" role="img" aria-label="Photo of a German Shepherd puppy lying beside a Siamese kitten on a white background"></div>
    </section>
    <div class="card__rule"></div>
    <section class="card__band">
      <div class="holder">
        <p class="holder__name">Tomás R. Quintaval</p>
        <p class="holder__credentials">DVM, MLAS, BS</p>
      </div>
      <span class="band-divider"></span>
      <ul class="contact">
        <li class="contact__item">
          <svg class="contact__icon" viewBox="0 0 24 24" aria-hidden="true"><path d="M6.6 10.8a15.1 15.1 0 0 0 6.6 6.6l2.2-2.2c.3-.3.7-.4 1-.2 1.1.4 2.3.6 3.6.6.6 0 1 .4 1 1V20c0 .6-.4 1-1 1A17 17 0 0 1 3 4c0-.6.4-1 1-1h3.5c.6 0 1 .4 1 1 0 1.3.2 2.5.6 3.6.1.3 0 .7-.2 1z"/></svg>
          <span>5552846017</span>
        </li>
        <li class="contact__item">
          <svg class="contact__icon" viewBox="0 0 24 24" aria-hidden="true"><path d="M2 5h20v14H2z" fill="none" stroke="#fff" stroke-width="2"/><path d="M2 5l10 8 10-8" fill="none" stroke="#fff" stroke-width="2"/></svg>
          <span>dvmtrq@mailbrook.net</span>
        </li>
      </ul>
    </section>
  </article>
</main>
</body>
</html>
```